Medical Billing Company Needs a Business Card Design

We need a business card design for a Florida based medical billing company called 'Clinicians Keystone Solutions'. We specialize in providing revenue cycle management services to physician and therapist offices (we're basically their back-office processing partner for providing billing software, claims submissions, A/R follow-up and patient statements & collections. Our logo is red and blue-ish, so make sure that whatever other elements are used will match appropriately. Our current business card design has a too small font size. I'd like to project an image that shows we are modern & reliable. On a side note, I'm planning on using ZUB for printing these cards.

Target Market(s)

Office managers, physicians, therapists

Industry/Entity Type

Printing

Requirements
Must have
• Logo
Name of Employee
Phone
Fax
E-mail
Website

```html
<!DOCTYPE html>
<html lang="en">
<head>
<meta charset="utf-8">
<title>Clinicians Keystone Solutions – Business Card</title>
<link rel="stylesheet" href="https://fonts.googleapis.com/css2?family=Open+Sans:wght@400;600;700&display=swap">
<style>
  :root {
    --stage: #ecebef;
    --paper: #ffffff;
    --indigo: #2c1a78;
    --indigo-light: #5a3f9c;
    --indigo-deep: #22105f;
    --crimson: #a5101c;
    --ink: #3a3a3a;
    --white: #ffffff;
  }
  * { box-sizing: border-box; margin: 0; padding: 0; }
  html, body { width: 1200px; height: 720px; overflow: hidden; }
  body {
    background: var(--stage);
    font-family: "Open Sans", Arial, sans-serif;
    position: relative;
  }
  .card {
    position: absolute;
    top: 206px;
    width: 540px;
    height: 309px;
    overflow: hidden;
    box-shadow: 0 6px 18px rgba(0,0,0,.18);
  }
  .card--front { left: 40px; background: var(--paper); }
  .card--back {
    left: 620px;
    background: linear-gradient(110deg, var(--indigo-light) 0%, var(--indigo) 55%, var(--indigo-deep) 100%);
  }
  .front-swoosh { position: absolute; inset: 0; }

  .brand {
    position: absolute;
    left: 36px;
    top: 92px;
    display: flex;
    align-items: center;
    gap: 9px;
  }
  .brand__mark { width: 12px; height: 12px; background: var(--crimson); }
  .brand__name {
    font-weight: 600;
    font-size: 18px;
    letter-spacing: 1px;
    text-transform: uppercase;
    color: var(--indigo);
    white-space: nowrap;
  }

  .person { position: absolute; left: 40px; top: 184px; }
  .person__name { font-weight: 700; font-size: 17px; color: var(--indigo); line-height: 1.2; }
  .person__title { font-size: 12px; color: var(--crimson); margin-bottom: 4px; }
  .person__address { font-size: 12px; color: var(--ink); line-height: 1.4; }

  .contact {
    position: absolute;
    right: 20px;
    top: 140px;
    list-style: none;
    color: var(--white);
    font-size: 12px;
    line-height: 1;
  }
  .contact__item {
    display: flex;
    align-items: center;
    justify-content: flex-end;
    gap: 6px;
    margin-bottom: 7px;
    white-space: nowrap;
  }
  .contact__item--gap { margin-top: 14px; }
  .contact__item svg { width: 12px; height: 12px; flex: none; }

  .back-brand {
    position: absolute;
    left: 0; right: 0;
    top: 110px;
    display: flex;
    justify-content: center;
    align-items: center;
    gap: 12px;
  }
  .back-brand__mark { width: 18px; height: 18px; border: 2px solid var(--white); }
  .back-brand__name {
    font-weight: 600;
    font-size: 24px;
    letter-spacing: 2px;
    text-transform: uppercase;
    color: var(--white);
  }
  .back-web {
    position: absolute;
    left: 0; right: 0;
    bottom: 58px;
    text-align: center;
    color: var(--white);
    font-size: 15px;
    letter-spacing: 3px;
  }
</style>
</head>
<body>

<section class="card card--front" aria-label="Business card front">
  <svg class="front-swoosh" viewBox="0 0 540 309" preserveAspectRatio="none" aria-hidden="true">
    <path d="M320 0 L540 0 L540 309 L110 309 C250 260 320 150 320 0 Z" fill="var(--crimson)"/>
    <path d="M360 0 L540 0 L540 309 L160 309 C290 260 360 150 360 0 Z" fill="var(--indigo)"/>
  </svg>

  <div class="brand">
    <span class="brand__mark"></span>
    <span class="brand__name">Clinicians Keystone</span>
  </div>

  <ul class="contact">
    <li class="contact__item">
      <svg viewBox="0 0 12 12"><circle cx="6" cy="6" r="5.5" fill="none" stroke="#fff"/><path d="M4 3.2 L5 4.6 L4.6 5.2 Q5.4 6.8 6.8 7.4 L7.4 7 L8.8 8 L8 9 Q4 8.4 3 4 Z" fill="#fff"/></svg>
      123-456-0789
    </li>
    <li class="contact__item">
      <svg viewBox="0 0 12 12"><rect x="3" y="1" width="6" height="4" fill="none" stroke="#fff"/><rect x="1" y="5" width="10" height="6" rx="1" fill="#fff"/></svg>
      123-456-0789
    </li>
    <li class="contact__item contact__item--gap">
      <svg viewBox="0 0 12 12"><rect x="0.5" y="2.5" width="11" height="7" fill="#fff"/><path d="M0.5 2.5 L6 7 L11.5 2.5" fill="none" stroke="var(--indigo)"/></svg>
      info@clinicianskeystone.com
    </li>
    <li class="contact__item">
      <svg viewBox="0 0 12 12"><circle cx="6" cy="6" r="5.5" fill="#fff"/><ellipse cx="6" cy="6" rx="2.4" ry="5.5" fill="none" stroke="var(--indigo)"/><path d="M0.5 6 H11.5" stroke="var(--indigo)"/></svg>
      www.clinicianskeystone.com
    </li>
  </ul>

  <div class="person">
    <p class="person__name">Your Name</p>
    <p class="person__title">Title</p>
    <p class="person__address">Street Name, City Name<br>State Zip Code</p>
  </div>
</section>

<section class="card card--back" aria-label="Business card back">
  <div class="back-brand">
    <span class="back-brand__mark"></span>
    <span class="back-brand__name">Clinicians Keystone</span>
  </div>
  <p class="back-web">www.clinicianskeystone.com</p>
</section>

</body>
</html>
```